Real estate broker business card

Want a modern celan but effective business card for my residential and commercial real estate business. I want the back of the card to advertise my services and to capture business. I have attached the back of my current business card fore ideas
Updates

Logos, photo and text updates added! Added Saturday, September 3, 2016

Project Deadline Extended Reason: LOGOS, PHOTOS AND TEST JUST UPLOADED! I'M READY TO PICK A DESIGN! THANK YOU! Added Saturday, September 3, 2016

Target Market(s)

home buyers and seller. commercial buyers and sellers

Industry/Entity Type

Real Estate

Contact Information for Business Card

must have my contact information and my photo

Requirements
Must have
• Carla Ventrino
• Owner & Qualifying Broker
• Ventrino Real Estate Services
• 505.718.2094
• carla@ventrinohomes.example
• www.ventrinohomes.example
Nice to have
• metallic
• Business capture text: " Don't buy or lease property without someone looking out for your best interests. I will represent you on your home or investment purchase for FREE!"
• "Home owners, call today to receive a FREE market analysis for your homes value!

```html
<!DOCTYPE html>
<html lang="en">
<head>
<meta charset="utf-8">
<title>Ventrino Real Estate Services – Business Card</title>
<link rel="stylesheet" href="https://fonts.googleapis.com/css2?family=Open+Sans:wght@400;600&display=swap">
<style>
  :root {
    --backdrop: #e9e6e3;
    --card: #1f2a33;
    --ink: #ffffff;
    --ink-soft: #dfe5ea;
    --teal: #1aa3b4;
    --photo-light: #d9d2cc;
    --photo-dark: #3a2c28;
  }
  * { margin: 0; padding: 0; box-sizing: border-box; }
  html, body { width: 1200px; height: 900px; overflow: hidden; }
  body {
    background: var(--backdrop);
    font-family: "Open Sans", sans-serif;
    position: relative;
  }
  .card {
    position: absolute;
    background: var(--card);
    color: var(--ink);
    box-shadow: 0 6px 18px rgba(0,0,0,0.25);
  }
  .card--front { left: 238px; top: 62px; width: 555px; height: 342px; }
  .card--back { left: 457px; top: 518px; width: 560px; height: 342px; }

  .brand-mark {
    position: absolute;
    left: 70px; top: 150px;
    display: flex; align-items: center; gap: 8px;
    font-weight: 600; font-size: 20px; letter-spacing: 2px;
    color: var(--teal);
  }
  .brand-mark .dot { width: 12px; height: 12px; background: var(--teal); }

  .details { position: absolute; left: 278px; top: 86px; }
  .details .name { font-weight: 600; font-size: 18px; line-height: 24px; }
  .details .title { font-size: 15px; color: var(--ink-soft); line-height: 20px; }
  .details .company { font-size: 15px; margin-top: 36px; line-height: 20px; color: var(--ink-soft); }
  .contact { list-style: none; margin-top: 4px; }
  .contact li {
    display: flex; align-items: center; gap: 8px;
    font-size: 15px; line-height: 20px; color: var(--ink-soft);
  }
  .contact svg { width: 12px; height: 12px; fill: var(--ink-soft); flex: none; }

  .wordmark {
    position: absolute;
    left: 45px; top: 150px;
    display: flex; align-items: center; gap: 14px;
    color: var(--teal);
    font-weight: 600;
  }
  .wordmark .dot { width: 16px; height: 16px; border-radius: 50%; background: var(--teal); flex: none; }
  .wordmark .lines { display: flex; flex-direction: column; }
  .wordmark .name { font-size: 34px; line-height: 40px; letter-spacing: 1px; }
  .wordmark .tagline { font-size: 12px; line-height: 16px; letter-spacing: 2.4px; }

  .portrait {
    position: absolute;
    left: 388px; top: 82px;
    width: 140px; height: 178px;
    background: linear-gradient(180deg, var(--photo-dark) 0%, #7a5f55 45%, var(--photo-light) 75%, #f4f1ee 100%);
    border-radius: 60px 60px 6px 6px;
    box-shadow: 0 4px 10px rgba(0,0,0,0.4);
  }
</style>
</head>
<body>
  <section class="card card--front" aria-label="Card front">
    <div class="brand-mark"><span class="dot"></span>VENTRINO</div>
    <div class="details">
      <p class="name">Carla Ventrino</p>
      <p class="title">Owner &amp; Qualifying Broker</p>
      <p class="company">Ventrino Real Estate Services</p>
      <ul class="contact">
        <li><svg viewBox="0 0 24 24"><path d="M6.6 10.8a15.1 15.1 0 0 0 6.6 6.6l2.2-2.2a1 1 0 0 1 1-.25 11.4 11.4 0 0 0 3.6.57 1 1 0 0 1 1 1V20a1 1 0 0 1-1 1A17 17 0 0 1 3 4a1 1 0 0 1 1-1h3.5a1 1 0 0 1 1 1 11.4 11.4 0 0 0 .57 3.6 1 1 0 0 1-.25 1z"/></svg>505.718.2094</li>
        <li><svg viewBox="0 0 24 24"><path d="M2 5h20v14H2z M2 5l10 8 10-8" fill="none" stroke="#dfe5ea" stroke-width="2.5"/></svg>carla@ventrinohomes.example</li>
        <li><svg viewBox="0 0 24 24"><circle cx="12" cy="12" r="10"/></svg>www.ventrinohomes.example</li>
      </ul>
    </div>
  </section>

  <section class="card card--back" aria-label="Card back">
    <div class="wordmark">
      <span class="dot"></span>
      <div class="lines">
        <span class="name">VENTRINO</span>
        <span class="tagline">REAL ESTATE SERVICES</span>
      </div>
    </div>
    <div class="portrait" role="img" aria-label="Portrait photo of the broker"></div>
  </section>
</body>
</html>
```